New Business Card Design Project

Use the flyer uploaded and website www.brightoakbuilders.com for inspiration.
List Our Services on Backside of business cards
Marcus Delling
Harborline Builders Inc.
Licensed General Contractors
858-471-6093

Contact Information for Business Card

Use the flyer uploaded and website www.brightoakbuilders.com for inspiration. List Our Services on Backside of business cards Marcus Delling Harborline Builders Inc. Licensed General Contractors 858-471-6093

```html
<!DOCTYPE html>
<html lang="en">
<head>
<meta charset="utf-8">
<title>Harborline Builders – Business Card</title>
<link rel="stylesheet" href="https://fonts.googleapis.com/css2?family=Cinzel:wght@400;600&family=Montserrat:wght@400&display=swap">
<style>
  :root {
    --bg: #e4e5e8;
    --card: #f6f6f6;
    --ink: #1c1c1c;
    --ink-soft: #3d3d3d;
    --rule: #6a6a6a;
  }
  html, body {
    margin: 0;
    width: 1200px;
    height: 958px;
    overflow: hidden;
    background: var(--bg);
  }
  .card {
    position: absolute;
    left: 286px;
    width: 627px;
    height: 358px;
    background: linear-gradient(120deg, #ececec 0%, var(--card) 45%, #ffffff 100%);
    box-shadow: 0 12px 24px rgba(0,0,0,0.18);
  }
  .card--front { top: 77px; }
  .card--back  { top: 525px; }

  .person {
    position: absolute;
    left: 36px;
    top: 158px;
  }
  .person__name {
    font-family: "Cinzel", serif;
    font-weight: 600;
    font-size: 21px;
    letter-spacing: 0.5px;
    color: var(--ink);
    line-height: 1;
  }
  .person__role {
    font-family: "Montserrat", sans-serif;
    font-size: 14px;
    color: var(--ink-soft);
    margin-top: 5px;
    letter-spacing: 0.3px;
  }

  .brand {
    position: absolute;
    display: flex;
    flex-direction: column;
    align-items: center;
    gap: 14px;
  }
  .brand__dot {
    width: 18px;
    height: 18px;
    border: 1.5px solid var(--ink);
    border-radius: 50%;
  }
  .brand__name {
    font-family: "Cinzel", serif;
    font-weight: 400;
    color: var(--ink);
    white-space: nowrap;
    letter-spacing: 0.5px;
  }
  .card--front .brand { left: 334px; width: 232px; top: 112px; }
  .card--front .brand__name { font-size: 20px; }
  .card--back .brand { left: 0; width: 627px; top: 150px; }
  .card--back .brand__name { font-size: 26px; }

  .contacts {
    position: absolute;
    left: 334px;
    top: 248px;
    margin: 0;
    padding: 0;
    list-style: none;
    font-family: "Montserrat", sans-serif;
    font-size: 14.5px;
    color: var(--ink-soft);
  }
  .contacts li {
    display: flex;
    align-items: center;
    gap: 7px;
    height: 27px;
  }
  .contacts svg { width: 11px; height: 11px; fill: var(--ink); }

  .divider {
    position: absolute;
    left: 59px;
    width: 510px;
    top: 258px;
    border-top: 1px solid var(--rule);
  }
  .services {
    position: absolute;
    left: 0;
    width: 627px;
    top: 276px;
    text-align: center;
    font-family: "Montserrat", sans-serif;
    font-size: 14px;
    line-height: 23px;
    color: var(--ink-soft);
    margin: 0;
  }
</style>
</head>
<body>

<section class="card card--front">
  <div class="person">
    <div class="person__name">MARCUS DELLING</div>
    <div class="person__role">Licensed General Contractors</div>
  </div>

  <div class="brand">
    <span class="brand__dot"></span>
    <span class="brand__name">HARBORLINE BUILDERS</span>
  </div>

  <ul class="contacts">
    <li>
      <svg viewBox="0 0 24 24" aria-hidden="true"><path d="M6.6 10.8a15.1 15.1 0 0 0 6.6 6.6l2.2-2.2a1 1 0 0 1 1-.25 11.4 11.4 0 0 0 3.6.57 1 1 0 0 1 1 1V20a1 1 0 0 1-1 1A17 17 0 0 1 3 4a1 1 0 0 1 1-1h3.5a1 1 0 0 1 1 1c0 1.25.2 2.45.57 3.6a1 1 0 0 1-.25 1z"/></svg>
      858-471-6093
    </li>
    <li>
      <svg viewBox="0 0 24 24" aria-hidden="true"><path d="M2 5h20v14H2z M2 5l10 8 10-8" stroke="#f6f6f6" stroke-width="1.5"/></svg>
      info@brightoakbuilders.com
    </li>
    <li>
      <svg viewBox="0 0 24 24" aria-hidden="true"><circle cx="12" cy="12" r="10"/><path d="M2 12h20M12 2c3 3 3 17 0 20M12 2c-3 3-3 17 0 20" stroke="#f6f6f6" stroke-width="1.3" fill="none"/></svg>
      www.brightoakbuilders.com
    </li>
  </ul>
</section>

<section class="card card--back">
  <div class="brand">
    <span class="brand__dot"></span>
    <span class="brand__name">HARBORLINE BUILDERS</span>
  </div>
  <div class="divider"></div>
  <p class="services">
    Painting • Flooring • Kitchens • Custom Renovations<br>
    Bathrooms • Energy Efficient Upgrades
  </p>
</section>

</body>
</html>
```